Design a product reviews website

We need a website design and simple logo for the brand Venlotix.com. The website will provide reviews of technology products and services. The brand and website should be approachable but should also be trustworthy and high quality. The deliverable should be designs, specs and assets that I can provide to a development team to build the website.

Target Market(s)

People researching products to buy.

Industry/Entity Type

Product

Logo Text

Venlotix.com

Number of Pages Required

5+ page

Font styles to use
Sans Serif

Colors
0492cd
0355a3
3176b5
33a6d7
85cae6
85abd2
cedeed
cee9f5

Requirements
Must have
• - Designs for the Homepage, Category and Article pages.
• - Designs for web and mobile.
• - Designs details for the engineering team to use for development.
• - I'm open to other colors than the preferences I chose but I'm more likely to like blues, greys and blacks.

```html
<!DOCTYPE html>
<html lang="en">
<head>
<meta charset="utf-8">
<title>Venlotix.com — Product Reviews</title>
<link rel="stylesheet" href="https://fonts.googleapis.com/css2?family=Bitter:wght@400;500;600;700&family=Montserrat:wght@600;700&display=swap">
<style>
:root{
  --blue-deep:#0355a3;
  --blue-mid:#3176b5;
  --blue-bright:#33a6d7;
  --blue-bar:#2c6cb0;
  --ink:#222;
  --text:#444;
  --muted:#777;
  --page:#f4f4f4;
  --line:#dcdcdc;
  --white:#fff;
  --footer:#262626;
  --footer-line:#3c3c3c;
  --star:#f39c12;
  --star-off:#b5b5b5;
}
*{box-sizing:border-box;margin:0;padding:0}
html,body{width:1200px;height:2985px;overflow:hidden}
body{position:relative;background:var(--page);font-family:"Bitter",Georgia,serif;color:var(--text)}
.abs{position:absolute}
a{color:inherit}

/* header */
.site-header{left:0;top:0;width:1200px;height:76px;background:var(--white);box-shadow:0 1px 4px rgba(0,0,0,.12);z-index:2}
.logo{left:86px;top:22px;font:700 27px/32px "Montserrat",Arial,sans-serif;color:var(--ink);letter-spacing:.5px}
.search{left:844px;top:20px;width:220px;height:38px;border:1px solid #9ab;border-radius:4px;font-size:12px;color:#333;padding:11px 12px}
.search svg{position:absolute;right:10px;top:10px}
.menu-btn{left:1080px;top:20px;width:37px;height:37px;background:var(--blue-deep);border-radius:5px}
.menu-btn i{position:absolute;left:11px;width:15px;height:2px;background:#fff}

/* hero */
.hero{left:0;top:76px;width:1200px;height:610px;background:linear-gradient(100deg,#b9c0c2 0%,#8f999e 35%,#6f7c86 65%,#5f7ea5 100%)}
.hero-visual{left:527px;top:40px;width:628px;height:500px;border-radius:8px;background:radial-gradient(ellipse at 55% 45%,#6aa7d8 0%,#3f6e9e 40%,rgba(190,195,200,.6) 75%,rgba(190,195,200,0) 100%)}
.hero-band{left:0;top:212px;width:620px;height:174px;background:linear-gradient(90deg,rgba(35,38,42,.88),rgba(35,38,42,.55) 80%,rgba(35,38,42,0))}
.hero-kicker{left:86px;top:250px;font:700 18px/22px "Montserrat",Arial,sans-serif;color:#fff}
.hero-title{left:86px;top:280px;font:700 29px/38px "Montserrat",Arial,sans-serif;color:#fff}
.dots{left:543px;top:495px}
.dots i{display:inline-block;width:26px;height:26px;border:3px solid #fff;border-radius:50%;margin-right:16px}
.dots i.on{background:var(--blue-bright)}

/* sidebar */
.side-nav{left:72px;top:726px;width:262px;background:var(--blue-mid);box-shadow:0 1px 3px rgba(0,0,0,.2)}
.side-nav li{list-style:none;height:54px;border-bottom:1px solid rgba(255,255,255,.15);display:flex;align-items:center;padding-left:20px;color:#fff;font-size:15px;position:relative}
.side-nav li.active{background:var(--blue-deep)}
.side-nav li .ico{width:15px;height:15px;margin-right:14px;opacity:.7}
.side-nav li svg.chev{position:absolute;right:14px;top:20px}

/* section heads */
.sec-head{height:50px;background:var(--blue-deep);color:#fff;font:500 16px/50px "Bitter",Georgia,serif;padding-left:20px;letter-spacing:.3px}

/* product cards */
.card{background:var(--white);border:1px solid var(--line)}
.photo{display:block;width:100%}
.stars{font-size:20px;letter-spacing:4px;color:var(--star);line-height:20px}
.stars .off{color:var(--star-off)}
.card-body{padding:0 22px}
.card-title{font:500 19px/24px "Bitter",Georgia,serif;color:var(--ink)}
.card-text{font-size:13px;line-height:26px;color:var(--text)}
.meta-bar{position:absolute;left:0;bottom:0;width:100%;height:38px;background:var(--blue-bright);color:#fff;font-size:12px;font-style:italic;display:flex;align-items:center;padding-left:14px;gap:22px}
.meta-bar u{text-decoration:underline}
.meta-bar .go{position:absolute;right:0;top:0;width:38px;height:38px;background:var(--blue-bar);display:flex;align-items:center;justify-content:center}
.avatar{display:inline-block;width:22px;height:22px;border-radius:50%;background:#e8e8e8;border:2px solid #fff;vertical-align:middle;margin-right:8px}
.meta-bar svg{vertical-align:middle;margin-right:6px}

.loading{left:362px;top:1956px;width:484px;height:38px;background:#fff;border:1px solid #aaa;border-radius:4px;text-align:center;font-size:12px;font-style:italic;line-height:36px;color:#333}

/* popular */
.pop{width:254px;height:255px}
.pop .stars-box{position:absolute;left:14px;top:128px;background:rgba(40,40,40,.75);padding:6px 10px;border-radius:2px;font-size:19px;letter-spacing:4px;color:var(--star);line-height:19px}
.pop .stars-box .off{color:var(--star-off)}
.pop-title{position:absolute;left:18px;top:196px;font:500 17px/22px "Bitter",Georgia,serif;color:var(--ink)}
.pop-meta{position:absolute;left:18px;top:224px;font-size:12px;font-style:italic;color:#444}
.pop-meta u{text-decoration:underline}
.pop-go{position:absolute;right:18px;top:202px;width:38px;height:38px;background:var(--blue-mid);display:flex;align-items:center;justify-content:center}

/* about */
.about{left:0;top:2040px;width:1200px;height:440px;background:linear-gradient(180deg,#3478bd,#2e6fb2)}
.about-visual{left:60px;top:30px;width:1080px;height:400px;background:radial-gradient(ellipse at 50% 60%,rgba(20,50,90,.28),rgba(20,50,90,0) 70%)}
.about-title{left:0;top:106px;width:1200px;text-align:center;font:400 38px/48px "Bitter",Georgia,serif;color:#fff}
.about-rule{left:560px;top:168px;width:80px;height:1px;background:rgba(255,255,255,.5)}
.about-text{left:205px;top:206px;width:790px;text-align:center;color:#fff;font:500 13.5px/28.5px "Bitter",Georgia,serif}

/* footer */
.footer{left:0;top:2480px;width:1200px;height:456px;background:var(--footer);color:#fff}
.newsletter{left:84px;top:51px;width:718px;height:70px;border:1px solid #8a8a8a;border-radius:3px}
.nl-label{position:absolute;left:58px;top:21px;font-size:19px}
.nl-input{position:absolute;left:242px;top:16px;width:360px;height:38px;background:#fff;color:#222;font-size:13px;padding:11px 10px}
.nl-btn{position:absolute;left:600px;top:16px;width:104px;height:38px;background:var(--blue-bright);font:600 12px/38px "Bitter",Georgia,serif;text-align:center;letter-spacing:.5px}
.follow{left:840px;top:70px;font-size:19px;font-weight:500}
.social{left:944px;top:68px}
.social i{display:inline-block;width:31px;height:31px;border-radius:50%;background:var(--blue-mid);border:2px solid #fff;margin-right:10px}
.f-head{font-size:22px;font-weight:400}
.f-head svg{vertical-align:-3px;margin-right:10px}
.f-rule{height:1px;background:var(--footer-line)}
.field{position:absolute;border:1px solid #999;border-radius:3px;font-size:13px;padding:11px 12px}
.submit{position:absolute;left:326px;top:938px;width:229px;height:40px;background:var(--blue-bright);border-radius:2px;text-align:center;font:600 14px/40px "Bitter",Georgia,serif;letter-spacing:.5px}
.links li{list-style:none;font-size:14px;line-height:27px}
.links li::before{content:"›";margin-right:10px}
.links li.current{font-weight:700}
.contact p{font-size:13px;line-height:23px;padding-left:28px;position:relative}
.contact svg{position:absolute;left:0;top:4px}
.v-line{width:1px;background:var(--footer-line)}

.bottom-line{left:0;top:2935px;width:1200px;height:6px;background:var(--blue-deep)}
.up-tab{left:584px;top:2918px}
.copyright{left:0;top:2941px;width:1200px;height:44px;background:#111;color:#fff;font-size:12px;text-align:center;line-height:44px}
</style>
</head>
<body>

<header class="site-header abs">
  <div class="logo abs">VENLOTIX.COM</div>
  <div class="search abs">Search Here
    <svg width="16" height="16" viewBox="0 0 16 16"><circle cx="6.5" cy="6.5" r="5" fill="none" stroke="#3176b5" stroke-width="1.6"/><path d="M10.2 10.2 15 15" stroke="#3176b5" stroke-width="1.8"/></svg>
  </div>
  <div class="menu-btn abs"><i style="top:12px"></i><i style="top:17px"></i><i style="top:22px"></i></div>
</header>

<section class="hero abs">
  <div class="hero-visual abs" role="img" aria-label="Laptop, tablet and smartphones showing colourful app screens"></div>
  <div class="hero-band abs"></div>
  <div class="hero-kicker abs">KNOW BEST DEAL ON</div>
  <h1 class="hero-title abs">HOME APPLIANCES &amp;<br>ELECTRONIC GADGETS</h1>
  <div class="dots abs"><i class="on"></i><i></i><i></i></div>
</section>

<nav class="abs">
<ul class="side-nav abs">
  <li class="active"><svg class="ico" viewBox="0 0 16 16"><path d="M1 8 8 2l7 6h-2v6H3V8z" fill="#fff"/></svg>Home<svg class="chev" width="8" height="13" viewBox="0 0 8 13"><path d="M1 1l5.5 5.5L1 12" fill="none" stroke="#fff" stroke-width="2"/></svg></li>
  <li><svg class="ico" viewBox="0 0 16 16"><rect x="2" y="3" width="12" height="10" fill="#fff"/></svg>Appliances<svg class="chev" width="8" height="13" viewBox="0 0 8 13"><path d="M1 1l5.5 5.5L1 12" fill="none" stroke="#fff" stroke-width="2"/></svg></li>
  <li><svg class="ico" viewBox="0 0 16 16"><rect x="1" y="2" width="14" height="9" fill="none" stroke="#fff" stroke-width="1.6"/><path d="M5 14h6" stroke="#fff" stroke-width="1.6"/></svg>Computers<svg class="chev" width="8" height="13" viewBox="0 0 8 13"><path d="M1 1l5.5 5.5L1 12" fill="none" stroke="#fff" stroke-width="2"/></svg></li>
  <li><svg class="ico" viewBox="0 0 16 16"><circle cx="8" cy="8" r="6" fill="none" stroke="#fff" stroke-width="1.6"/><circle cx="8" cy="8" r="2" fill="#fff"/></svg>Electronics<svg class="chev" width="8" height="13" viewBox="0 0 8 13"><path d="M1 1l5.5 5.5L1 12" fill="none" stroke="#fff" stroke-width="2"/></svg></li>
  <li><svg class="ico" viewBox="0 0 16 16"><path d="M1 5l12-2 2 4-12 3z" fill="#fff"/><path d="M5 10v4" stroke="#fff" stroke-width="1.6"/></svg>Home Security<svg class="chev" width="8" height="13" viewBox="0 0 8 13"><path d="M1 1l5.5 5.5L1 12" fill="none" stroke="#fff" stroke-width="2"/></svg></li>
  <li><svg class="ico" viewBox="0 0 16 16"><rect x="4" y="1" width="8" height="14" rx="1.5" fill="none" stroke="#fff" stroke-width="1.6"/></svg>Mobile<svg class="chev" width="8" height="13" viewBox="0 0 8 13"><path d="M1 1l5.5 5.5L1 12" fill="none" stroke="#fff" stroke-width="2"/></svg></li>
  <li><svg class="ico" viewBox="0 0 16 16"><rect x="1" y="3" width="10" height="8" fill="#fff"/><rect x="12" y="5" width="3" height="8" fill="#fff"/></svg>Smart Home<svg class="chev" width="8" height="13" viewBox="0 0 8 13"><path d="M1 1l5.5 5.5L1 12" fill="none" stroke="#fff" stroke-width="2"/></svg></li>
  <li><svg class="ico" viewBox="0 0 16 16"><circle cx="8" cy="8" r="6.5" fill="none" stroke="#fff" stroke-width="1.6"/><path d="M5 8l2 2 4-4" fill="none" stroke="#fff" stroke-width="1.6"/></svg>Software<svg class="chev" width="8" height="13" viewBox="0 0 8 13"><path d="M1 1l5.5 5.5L1 12" fill="none" stroke="#fff" stroke-width="2"/></svg></li>
</ul>
</nav>

<!-- latest products -->
<div class="sec-head abs" style="left:362px;top:728px;width:484px">LATEST PRODUCTS</div>

<article class="card abs" style="left:362px;top:788px;width:484px;height:368px">
  <div class="photo" role="img" aria-label="Black speaker system with two satellite speakers and subwoofer" style="height:175px;background:linear-gradient(180deg,#e9e9e9,#cfcfcf)"></div>
  <div class="card-body">
    <div class="stars" style="margin-top:16px">★★★★<span class="off">★</span></div>
    <h3 class="card-title" style="margin-top:18px">The Sonara Home Hub</h3>
    <p class="card-text" style="margin-top:6px">Lorem ipsum dolor sit amet, consectetuer adipiscing elit, sed diam nonummy nibh euismod tincidunt ut laoreet dolore magna</p>
  </div>
  <div class="meta-bar"><span><i class="avatar"></i>By John</span><span><svg width="12" height="12" viewBox="0 0 12 12"><rect x="1" y="2" width="10" height="9" fill="none" stroke="#fff"/><path d="M1 5h10" stroke="#fff"/></svg>On 11/08/2016</span><span><svg width="12" height="12" viewBox="0 0 12 12"><path d="M1 1h5l5 5-5 5-5-5z" fill="#fff"/></svg>In <u>Home</u>, <u>Speakers</u></span>
    <div class="go"><svg width="8" height="13" viewBox="0 0 8 13"><path d="M1 1l5.5 5.5L1 12" fill="none" stroke="#fff" stroke-width="2"/></svg></div></div>
</article>

<article class="card abs" style="left:362px;top:1182px;width:232px;height:356px">
  <div class="photo" role="img" aria-label="Built-in stainless kitchen appliances" style="height:173px;background:linear-gradient(180deg,#bdbdbd,#6e6e6e)"></div>
  <div class="card-body" style="padding:0 20px">
    <div class="stars" style="margin-top:16px">★★★★<span class="off">★</span></div>
    <h3 class="card-title" style="margin-top:16px;font-size:18px">Kitchen Appliances</h3>
    <p class="card-text" style="margin-top:4px">Lorem ipsum dolor sit amet, consectetuer adipiscing elit</p>
  </div>
  <div class="meta-bar"><span><svg width="12" height="12" viewBox="0 0 12 12"><path d="M1 1h5l5 5-5 5-5-5z" fill="#fff"/></svg>In <u>Home</u>, <u>Kitchen</u></span>
    <div class="go"><svg width="8" height="13" viewBox="0 0 8 13"><path d="M1 1l5.5 5.5L1 12" fill="none" stroke="#fff" stroke-width="2"/></svg></div></div>
</article>

<article class="card abs" style="left:615px;top:1182px;width:231px;height:356px">
  <div class="photo" role="img" aria-label="Juicer mixer grinder on a wooden counter" style="height:173px;background:linear-gradient(180deg,#6b5a4a,#3a2e25)"></div>
  <div class="card-body" style="padding:0 20px">
    <div class="stars" style="margin-top:16px">★★★★<span class="off">★</span></div>
    <h3 class="card-title" style="margin-top:16px;font-size:18px">Juicer Mixer Grinder</h3>
    <p class="card-text" style="margin-top:4px">Lorem ipsum dolor sit amet, consectetuer adipiscing elit</p>
  </div>
  <div class="meta-bar"><span><svg width="12" height="12" viewBox="0 0 12 12"><path d="M1 1h5l5 5-5 5-5-5z" fill="#fff"/></svg>In <u>Home</u>, <u>Kitchen</u></span>
    <div class="go"><svg width="8" height="13" viewBox="0 0 8 13"><path d="M1 1l5.5 5.5L1 12" fill="none" stroke="#fff" stroke-width="2"/></svg></div></div>
</article>

<article class="card abs" style="left:362px;top:1564px;width:484px;height:368px">
  <div class="photo" role="img" aria-label="Home theater setup with wall screen and tower speakers" style="height:173px;background:linear-gradient(180deg,#d9d6cf,#4a4541)"></div>
  <div class="card-body">
    <div class="stars" style="margin-top:16px">★★★★<span class="off">★</span></div>
    <h3 class="card-title" style="margin-top:18px">Home Theater</h3>
    <p class="card-text" style="margin-top:6px">Lorem ipsum dolor sit amet, consectetuer adipiscing elit, sed diam nonummy nibh euismod tincidunt ut laoreet dolore magna</p>
  </div>
  <div class="meta-bar"><span><i class="avatar"></i>By John</span><span><svg width="12" height="12" viewBox="0 0 12 12"><rect x="1" y="2" width="10" height="9" fill="none" stroke="#fff"/><path d="M1 5h10" stroke="#fff"/></svg>On 11/08/2016</span><span><svg width="12" height="12" viewBox="0 0 12 12"><path d="M1 1h5l5 5-5 5-5-5z" fill="#fff"/></svg>In <u>Home</u>, <u>Electronics</u></span>
    <div class="go"><svg width="8" height="13" viewBox="0 0 8 13"><path d="M1 1l5.5 5.5L1 12" fill="none" stroke="#fff" stroke-width="2"/></svg></div></div>
</article>

<div class="loading abs"><svg width="14" height="14" viewBox="0 0 14 14" style="vertical-align:-2px;margin-right:8px"><circle cx="7" cy="7" r="5.5" fill="none" stroke="#888" stroke-width="2" stroke-dasharray="4 3"/></svg>Loading</div>

<!-- popular products -->
<div class="sec-head abs" style="left:874px;top:728px;width:254px">POPULAR PRODUCTS</div>

<article class="card pop abs" style="left:874px;top:788px">
  <div class="photo" role="img" aria-label="Copper pots hanging on a tiled wall" style="height:175px;background:linear-gradient(180deg,#a9a39a,#8a4e2c)"></div>
  <div class="stars-box">★★★★<span class="off">★</span></div>
  <h3 class="pop-title">Copper Pots</h3>
  <div class="pop-meta">✎ In <u>Home</u>, <u>Utensils</u></div>
  <div class="pop-go"><svg width="8" height="13" viewBox="0 0 8 13"><path d="M1 1l5.5 5.5L1 12" fill="none" stroke="#fff" stroke-width="2"/></svg></div>
</article>

<article class="card pop abs" style="left:874px;top:1065px">
  <div class="photo" role="img" aria-label="Wireless speakers on a dark background" style="height:175px;background:linear-gradient(180deg,#2a2a2a,#0e0e0e)"></div>
  <div class="stars-box" style="background:none">★★★<span class="off">★★</span></div>
  <h3 class="pop-title">Wireless Speakers</h3>
  <div class="pop-meta">✎ In <u>Home</u>, <u>Speakers</u></div>
  <div class="pop-go"><svg width="8" height="13" viewBox="0 0 8 13"><path d="M1 1l5.5 5.5L1 12" fill="none" stroke="#fff" stroke-width="2"/></svg></div>
</article>

<article class="card pop abs" style="left:874px;top:1343px">
  <div class="photo" role="img" aria-label="White electric steam iron" style="height:175px;background:linear-gradient(180deg,#f1f1f1,#d3dbe2)"></div>
  <div class="stars-box">★★★<span class="off">★★</span></div>
  <h3 class="pop-title">Electrical Iron</h3>
  <div class="pop-meta">✎ In <u>Home</u>, <u>Utensils</u></div>
  <div class="pop-go"><svg width="8" height="13" viewBox="0 0 8 13"><path d="M1 1l5.5 5.5L1 12" fill="none" stroke="#fff" stroke-width="2"/></svg></div>
</article>

<article class="card pop abs" style="left:874px;top:1622px">
  <div class="photo" role="img" aria-label="Copper pots hanging on a tiled wall" style="height:175px;background:linear-gradient(180deg,#a9a39a,#8a4e2c)"></div>
  <div class="stars-box">★★★★<span class="off">★</span></div>
  <h3 class="pop-title">Copper Pots</h3>
  <div class="pop-meta">✎ In <u>Home</u>, <u>Utensils</u></div>
  <div class="pop-go"><svg width="8" height="13" viewBox="0 0 8 13"><path d="M1 1l5.5 5.5L1 12" fill="none" stroke="#fff" stroke-width="2"/></svg></div>
</article>

<!-- about -->
<section class="about abs">
  <div class="about-visual abs" role="img" aria-label="Faint collage of speakers, monitors and home electronics"></div>
  <h2 class="about-title abs">ABOUT VENLOTIX</h2>
  <div class="about-rule abs"></div>
  <p class="about-text abs">Lorem ipsum dolor sit amet, consectetuer adipiscing elit, sed diam nonummy nibh euismod tincidunt ut laoreet dolore magna aliquam erat volutpat. Ut wisi enim ad minim veniam, quis nostrud exerci tation ullamcorper suscipit lobortis nisl ut aliquip ex ea commodo consequat. Duis autem vel eum iriure dolor in hendrerit in vulputate velit esse molestie consequat, vel illum dolore eu feugiat nulla facilisis at vero eros et accumsan et iusto odio dignissim qui blandit praesent luptatum zzril delenit augue duis dolore te feugait nulla facilisi.</p>
</section>

<!-- footer -->
<footer class="footer abs">
  <div class="newsletter abs">
    <svg class="abs" style="left:16px;top:19px" width="30" height="28" viewBox="0 0 30 28"><path d="M2 11 15 2l13 9v15H2z" fill="#fff"/><path d="M2 11l13 9 13-9" fill="none" stroke="#262626" stroke-width="2"/></svg>
    <span class="nl-label">Newsletter Signup</span>
    <div class="nl-input">Enter your email here</div>
    <div class="nl-btn">SUBSCRIBE</div>
  </div>
  <div class="follow abs">Follow Us</div>
  <div class="social abs" aria-label="Social links"><i></i><i></i><i></i><i></i></div>

  <div class="abs" style="left:84px;top:163px;width:450px">
    <h4 class="f-head"><svg width="24" height="24" viewBox="0 0 24 24"><circle cx="12" cy="12" r="10.5" fill="none" stroke="#33a6d7" stroke-width="2"/><text x="12" y="17" text-anchor="middle" font-size="14" fill="#33a6d7" font-family="Bitter,serif">?</text></svg>Quick Inquiry</h4>
  </div>
  <div class="f-rule abs" style="left:84px;top:205px;width:472px"></div>
  <div class="field" style="left:84px;top:228px;width:224px;height:42px">Name</div>
  <div class="field" style="left:84px;top:286px;width:224px;height:42px">Email Address</div>
  <div class="field" style="left:84px;top:342px;width:224px;height:42px">Phone Number</div>
  <div class="field" style="left:326px;top:228px;width:229px;height:98px">Message</div>
  <div class="submit" style="top:342px">SUBMIT</div>

  <div class="v-line abs" style="left:593px;top:163px;height:262px"></div>

  <div class="abs" style="left:627px;top:166px">
    <h4 class="f-head"><svg width="18" height="22" viewBox="0 0 18 22"><rect x="1" y="3" width="16" height="18" fill="#33a6d7"/><rect x="5" y="1" width="8" height="4" fill="#fff"/></svg>Quick Links</h4>
  </div>
  <div class="f-rule abs" style="left:627px;top:205px;width:200px"></div>
  <ul class="links abs" style="left:630px;top:216px">
    <li class="current">Home</li><li>About Us</li><li>Our Products</li><li>Support</li><li>Faqs</li><li>Contact Us</li>
  </ul>

  <div class="v-line abs" style="left:832px;top:163px;height:262px"></div>

  <div class="abs" style="left:868px;top:163px">
    <h4 class="f-head"><svg width="22" height="22" viewBox="0 0 22 22"><circle cx="11" cy="11" r="9.5" fill="none" stroke="#33a6d7" stroke-width="2"/><path d="M2 11h18M11 2c-4 5-4 13 0 18M11 2c4 5 4 13 0 18" fill="none" stroke="#33a6d7" stroke-width="1.4"/></svg>Contact Information</h4>
  </div>
  <div class="f-rule abs" style="left:868px;top:205px;width:262px"></div>
  <div class="contact abs" style="left:870px;top:230px;width:270px">
    <p><svg width="14" height="18" viewBox="0 0 14 18"><path d="M7 17S1 10 1 6.5a6 6 0 0 1 12 0C13 10 7 17 7 17z" fill="#fff"/><circle cx="7" cy="6.5" r="2" fill="#262626"/></svg>VENLOTIX,<br>Lorem ipsum dolor sit amet,<br>consec tetuer adipiscing elit, sed</p>
    <p style="margin-top:22px"><svg width="16" height="16" viewBox="0 0 16 16"><path d="M3 1l3 3-2 2c1 2.5 3.5 5 6 6l2-2 3 3-2 2C7 15 1 9 1 3z" fill="#fff"/></svg><b>123-456-7890</b></p>
    <p style="margin-top:26px"><svg width="16" height="12" viewBox="0 0 16 12"><rect x="0" y="1" width="16" height="11" fill="#fff"/><path d="M0 1l8 6 8-6" fill="none" stroke="#262626" stroke-width="1.4"/></svg>info@venlotix.com</p>
  </div>
</footer>

<div class="bottom-line abs"></div>
<svg class="up-tab abs" width="32" height="18" viewBox="0 0 32 18"><path d="M0 18 10 4Q16-2 22 4l10 14z" fill="#0355a3"/><path d="M11 12l5-5 5 5" fill="none" stroke="#fff" stroke-width="1.6"/></svg>
<div class="copyright abs">Copyright 2016 <b>VENLOTIX</b> | All Right Reserved.</div>

</body>
</html>
```